Beacon Advisory Website

I currently have a website www.beaconadvisoryinc.com. We are a IT Consulting Company. Our website will pretty much tell out our services. I am looking to enhance my website and make it look more professional. Looking for very classy and Contemporary look and design for my website.

It Company

```html
<!DOCTYPE html>
<html lang="en">
<head>
<meta charset="utf-8">
<title>Beacon Advisory</title>
<link rel="stylesheet" href="https://fonts.googleapis.com/css2?family=Lato:wght@400;700&family=Oswald:wght@400&family=Questrial&display=swap">
<style>
:root{
  --brand:#0d3a85;
  --brand-deep:#0a2f6e;
  --ink:#222;
  --white:#fff;
  --footer:#2a2a2a;
  --footer-line:#3a3a3a;
  --muted:#c9c9c9;
  --card:#151515;
}
*{box-sizing:border-box;margin:0;padding:0}
html,body{width:1010px;height:1200px;overflow:hidden}
body{position:relative;font-family:"Lato",sans-serif;color:var(--ink);background:var(--white)}
.abs{position:absolute}

.topbar{left:0;top:0;width:1010px;height:27px;background:var(--brand)}
.topbar .phone{left:662px;top:5px;color:var(--white);font:700 13px "Lato",sans-serif;display:flex;align-items:center;gap:6px}
.social-top{left:810px;top:0;display:flex}
.social-top span{width:29px;height:27px;border-left:1px solid #2a55a0;background:#124592}

.header{left:0;top:27px;width:1010px;height:70px;background:var(--white)}
.brand{left:84px;top:22px;display:flex;align-items:center;gap:8px}
.brand .dot{width:26px;height:26px;border-radius:50%;background:var(--brand)}
.brand b{font:700 22px "Lato",sans-serif;color:var(--brand);letter-spacing:.5px}
.nav{left:386px;top:24px;display:flex;align-items:center}
.nav a{font:400 14px "Questrial",sans-serif;color:#333;text-decoration:none;padding:0 9px;border-left:1px solid #ddd;line-height:16px}
.nav .home{border:none;padding:0 9px 0 0}

.hero{left:0;top:97px;width:1010px;height:541px;background:radial-gradient(ellipse at 68% 35%,#9cc3e0 0%,#5a86ab 28%,#2f4a66 58%,#1e2e42 100%)}
.hero-title{left:85px;top:204px;width:380px;font:400 24.5px/30px "Oswald",sans-serif;color:var(--white);text-shadow:0 1px 3px rgba(0,0,0,.5)}
.cta{left:83px;top:318px;width:211px;height:44px;background:var(--brand);border:2px solid var(--white);color:var(--white);font:700 17px/40px "Lato",sans-serif;text-align:center}

.card{top:446px;width:256px;height:151px;background:var(--card);border-radius:3px;box-shadow:0 4px 10px rgba(0,0,0,.4)}
.card .tab{position:absolute;left:-4px;top:6px;width:230px;height:31px;background:var(--white);clip-path:polygon(0 0,100% 0,92% 100%,0 100%);font:400 15px/31px "Questrial",sans-serif;color:var(--brand);padding-left:12px;letter-spacing:.3px}
.card .icon{position:absolute;left:16px;top:52px;width:66px;height:66px;border-radius:50%;background:var(--brand);border:2px solid #fff;display:flex;align-items:center;justify-content:center}
.card p{position:absolute;left:95px;top:52px;width:152px;font:400 10px/14px "Lato",sans-serif;color:var(--white)}
.card .more{position:absolute;right:22px;top:131px;font:400 10px "Lato",sans-serif;color:var(--white);text-decoration:underline}

.welcome{left:0;top:674px;width:1010px;text-align:center;font:400 24px "Questrial",sans-serif;color:var(--ink);display:flex;justify-content:center;align-items:center;gap:10px}
.welcome .dot{width:26px;height:26px;border-radius:50%;background:var(--brand)}
.welcome strong{color:var(--brand);font-weight:700;font-family:"Lato",sans-serif}
.rule{left:224px;top:711px;width:562px;border-top:1px dotted #888}
.points{left:84px;top:733px;width:470px;list-style:none}
.points li{position:relative;padding-left:27px;font:400 12.5px/16px "Lato",sans-serif;color:#222;margin-bottom:12px}
.points svg{position:absolute;left:0;top:3px}
.video{left:590px;top:738px;width:336px;height:220px;background:linear-gradient(180deg,#f4f4f4,#d9c3b0);border-radius:6px}

.footer{left:0;top:958px;width:1010px;height:205px;background:var(--footer)}
.fcol h3{font:700 15px "Lato",sans-serif;color:var(--white);letter-spacing:.5px;padding-bottom:7px;border-bottom:1px solid var(--footer-line)}
.links{left:86px;top:981px;width:108px}
.links ul{list-style:none;margin-top:6px}
.links li{font:400 11px/19.5px "Lato",sans-serif;color:var(--white)}
.links li::before{content:"»";color:#aaa;margin-right:12px;font-size:10px}
.contact{left:266px;top:981px;width:164px}
.contact .row{display:flex;gap:8px;margin-top:8px;font:400 11px/15px "Lato",sans-serif;color:var(--white)}
.inquiry{left:503px;top:981px;width:192px}
.inquiry .field{margin-top:8px;width:182px;height:22px;background:var(--white);border-radius:2px;font:400 10px/22px "Lato",sans-serif;color:#555;padding-left:7px}
.inquiry .msg{height:36px;line-height:14px;padding-top:4px}
.inquiry .submit{margin-top:9px;width:54px;height:21px;background:var(--brand);color:var(--white);font:700 11px/21px "Lato",sans-serif;text-align:center}
.fbrand{left:770px;top:1025px;font:700 18px "Lato",sans-serif;color:#bdbdbd;letter-spacing:.5px}
.fsocial{left:784px;top:1091px;display:flex;gap:7px}
.fsocial span{width:26px;height:26px;border-radius:50%}
.divider{top:1005px;width:1px;height:110px;background:#3c3c3c}

.copyright{left:0;top:1163px;width:1010px;height:37px;background:var(--brand);color:var(--white);font:400 11px/37px "Lato",sans-serif;text-align:center}
</style>
</head>
<body>

<div class="abs topbar"></div>
<div class="abs topbar-inner"></div>
<div class="abs phone" style="left:662px;top:5px;color:#fff;font:700 13px 'Lato',sans-serif;display:flex;align-items:center;gap:6px">
  <svg width="12" height="14" viewBox="0 0 12 14"><path d="M3 1l2 3-1.5 1.5c.8 2 2 3.2 4 4L9 8l3 2-1.5 2.5C6 12.5 1.5 8 1 2.5z" fill="#fff"/></svg>
  +1 (555) 310 8820
</div>
<div class="abs social-top"><span></span><span></span><span></span><span></span></div>

<div class="abs header"></div>
<div class="abs brand"><span class="dot"></span><b>BEACON ADVISORY</b></div>
<nav class="abs nav" style="top:51px">
  <a class="home" href="#"><svg width="18" height="16" viewBox="0 0 18 16"><path d="M9 1L1 8h2.5v7h4v-4h3v4h4V8H17z" fill="#0d3a85"/></svg></a>
  <a href="#">COMPANY</a><a href="#">SERVICES</a><a href="#">SOLUTIONS</a><a href="#">RESOURCES</a><a href="#">CAREER</a><a href="#" style="padding-right:0">CONTACT US</a>
</nav>

<section class="abs hero" role="img" aria-label="Businessman holding glowing blue gears with industry diagrams"></section>
<h1 class="abs hero-title">We Will Delivers Highest Level Of Quality Consultants And Services For The Lowest Cost Of Ownership</h1>
<div class="abs cta">GET STARTED WITH US</div>

<article class="abs card" style="left:83px">
  <div class="tab">CONSULTING</div>
  <div class="icon"><svg width="30" height="30" viewBox="0 0 30 30"><circle cx="12" cy="11" r="5" fill="#fff"/><path d="M3 28c0-7 4-10 9-10s9 3 9 10z" fill="#fff"/><rect x="16" y="2" width="12" height="8" rx="3" fill="none" stroke="#fff" stroke-width="1.5"/></svg></div>
  <p>Beacon Advisory has certified professional consultants to work with you to help increase the business by providing IT services...</p>
  <span class="more">Read More</span>
</article>
<article class="abs card" style="left:377px">
  <div class="tab">STAFF AUGMENTATION</div>
  <div class="icon"><svg width="34" height="28" viewBox="0 0 34 28"><circle cx="17" cy="8" r="4.5" fill="#fff"/><circle cx="7" cy="11" r="3.5" fill="#fff"/><circle cx="27" cy="11" r="3.5" fill="#fff"/><path d="M9 27c0-7 3-11 8-11s8 4 8 11z" fill="#fff"/><path d="M1 25c0-5 2-8 6-8s5 2 5 4v4zM33 25c0-5-2-8-6-8s-5 2-5 4v4z" fill="#fff"/></svg></div>
  <p>For years Beacon Advisory has been offering our customers the ability to augment their existing staff ...</p>
  <span class="more">Read More</span>
</article>
<article class="abs card" style="left:671px">
  <div class="tab">OFFSHORE</div>
  <div class="icon"><svg width="32" height="32" viewBox="0 0 32 32"><circle cx="16" cy="14" r="11" fill="none" stroke="#fff" stroke-width="1.5"/><path d="M5 14h22M16 3v22M8 7l16 14M24 7L8 21" stroke="#fff" stroke-width="1"/><circle cx="16" cy="20" r="3.5" fill="#fff"/><path d="M10 31c0-4 3-6 6-6s6 2 6 6z" fill="#fff"/></svg></div>
  <p>Our Offshore development model has a unique distinction of providing efficient software solutions ...</p>
  <span class="more">Read More</span>
</article>

<h2 class="abs welcome"><span class="dot"></span><span>WELCOME TO <strong>BEACON ADVISORY</strong></span></h2>
<div class="abs rule"></div>
<ul class="abs points">
  <li><svg width="13" height="13" viewBox="0 0 13 13"><circle cx="6.5" cy="6.5" r="6.5" fill="#0d3a85"/><path d="M3.5 6.8l2 2 4-4" stroke="#fff" stroke-width="1.6" fill="none"/></svg>Lorem ipsum dolor sit amet, consectetur adipiscing elit. Nulla fringilla bibendum its orci at convallis. Suspendisse a maximus turpis.</li>
  <li><svg width="13" height="13" viewBox="0 0 13 13"><circle cx="6.5" cy="6.5" r="6.5" fill="#0d3a85"/><path d="M3.5 6.8l2 2 4-4" stroke="#fff" stroke-width="1.6" fill="none"/></svg>Aenean sed blandit lectus, sed hendrerit felis. Etiam a elit eu nisi pulvinar interdudf.</li>
  <li><svg width="13" height="13" viewBox="0 0 13 13"><circle cx="6.5" cy="6.5" r="6.5" fill="#0d3a85"/><path d="M3.5 6.8l2 2 4-4" stroke="#fff" stroke-width="1.6" fill="none"/></svg>Praesent vel leo non enim rutrum lobortis vitae eu ante. Nulla fringilla bibendum eti orci at convallis. Suspendisse a maximus turpis.</li>
  <li><svg width="13" height="13" viewBox="0 0 13 13"><circle cx="6.5" cy="6.5" r="6.5" fill="#0d3a85"/><path d="M3.5 6.8l2 2 4-4" stroke="#fff" stroke-width="1.6" fill="none"/></svg>Nulla fringilla bibendum orci at convallis. Suspendisse a maximus turpis. Praeset vel leo non enim rutrum lobortis vitae eu ante.</li>
  <li><svg width="13" height="13" viewBox="0 0 13 13"><circle cx="6.5" cy="6.5" r="6.5" fill="#0d3a85"/><path d="M3.5 6.8l2 2 4-4" stroke="#fff" stroke-width="1.6" fill="none"/></svg>Praesent vel leo non enim rutrum lobortis vitae eu ante.</li>
</ul>
<div class="abs video" role="img" aria-label="Hands holding a tablet playing a company video"></div>

<footer class="abs footer"></footer>
<div class="abs divider" style="left:226px"></div>
<div class="abs divider" style="left:463px"></div>
<div class="abs divider" style="left:727px"></div>

<div class="abs fcol links">
  <h3>Quick Links</h3>
  <ul><li>Home</li><li>Company</li><li>Services</li><li>Solutions</li><li>Resources</li><li>Career</li><li>Contact Us</li></ul>
</div>
<div class="abs fcol contact">
  <h3>Contact Details</h3>
  <div class="row"><svg width="9" height="12" viewBox="0 0 9 12"><path d="M4.5 0A4.5 4.5 0 0 0 0 4.5C0 8 4.5 12 4.5 12S9 8 9 4.5A4.5 4.5 0 0 0 4.5 0zm0 6.3a1.8 1.8 0 1 1 0-3.6 1.8 1.8 0 0 1 0 3.6z" fill="#fff"/></svg><div><b>HEAD OFFICE</b><br>480 Harbor Line Rd<br>Suite 12<br>Millbrook, NJ 07999</div></div>
  <div class="row" style="margin-top:12px"><svg width="10" height="11" viewBox="0 0 12 14"><path d="M3 1l2 3-1.5 1.5c.8 2 2 3.2 4 4L9 8l3 2-1.5 2.5C6 12.5 1.5 8 1 2.5z" fill="#fff"/></svg>+1 (555) 310 8820</div>
  <div class="row" style="margin-top:14px"><svg width="12" height="9" viewBox="0 0 12 9"><rect x=".5" y=".5" width="11" height="8" fill="none" stroke="#fff"/><path d="M.5.5l5.5 4.5L11.5.5" fill="none" stroke="#fff"/></svg>info@beaconadvisory.com</div>
</div>
<div class="abs fcol inquiry">
  <h3>Quick Inquiry</h3>
  <div class="field" style="margin-top:11px">Name</div>
  <div class="field">Email</div>
  <div class="field msg">Message</div>
  <div class="submit">Submit</div>
</div>
<div class="abs fbrand">BEACON ADVISORY</div>
<div class="abs fsocial"><span style="background:#3b5998"></span><span style="background:#1da1f2"></span><span style="background:#e0202f"></span><span style="background:#dd4b39"></span></div>

<div class="abs copyright">Copyright © 2016 Beacon Advisory Inc.&nbsp; All Rights Reserved.</div>

</body>
</html>
```